Home Loan Introducer needs logo/business cards

We need a simple but classy logo for business cards and flyers. The business is a home loan referral business that is called an Introducer. The business name is "The Harborline".
I was thinking very simple and straight to the point on the front with "Home Loans" the only thing on the front with a nice background colour/s.
Then on the back, "The Harborline"
and "Quality Customer Service"
and "Email, text or call welcome"
and then my name, email address and phone number.
Updates
Thank you for all the designs :-)
Target Market(s)
Home buyers.
Home owners.
Investors.
Industry/Entity Type
Loan
Look and feel

```html
<!DOCTYPE html>
<html lang="en">
<head>
<meta charset="utf-8">
<title>The Harborline – Business Cards</title>
<link rel="stylesheet" href="https://fonts.googleapis.com/css2?family=Exo+2:wght@500;700;800&family=Ubuntu:wght@400;500&display=swap">
<style>
  :root {
    --canvas: #e9e6e1;
    --card-dark: #1d1d1d;
    --amber: #fbae34;
    --blue: #0f66b8;
    --white: #ffffff;
    --ink: #1a1a1a;
  }
  * { box-sizing: border-box; margin: 0; padding: 0; }
  html, body {
    width: 1200px; height: 750px; overflow: hidden;
    background: var(--canvas);
  }
  .canvas { position: relative; width: 1200px; height: 750px; }

  .card {
    position: absolute;
    width: 460px; height: 270px;
    background: var(--card-dark);
    overflow: hidden;
    box-shadow: 0 6px 18px rgba(0,0,0,0.25);
  }

  /* Contact side */
  .card--back { left: 160px; top: 60px; }
  .card--back .amber-band {
    position: absolute; left: 0; right: 0; bottom: 0; height: 96px;
    background: var(--amber);
  }
  .brand-label {
    position: absolute; left: 150px; top: 96px;
    display: flex; align-items: center; gap: 8px;
    background: var(--amber);
    border-radius: 4px;
    padding: 2px 12px 2px 8px;
  }
  .brand-label__mark { width: 11px; height: 11px; background: var(--blue); }
  .brand-label__name {
    font-family: "Exo 2", sans-serif;
    font-weight: 700; font-size: 18px; line-height: 22px;
    text-transform: uppercase;
    color: var(--blue);
    letter-spacing: 0.5px;
  }
  .benefits {
    position: absolute; left: 170px; top: 132px;
    list-style: none;
    font-family: "Exo 2", sans-serif; font-weight: 500;
    font-size: 13px; color: var(--blue); line-height: 17px;
  }
  .benefits li { display: flex; align-items: center; gap: 4px; }
  .benefits svg { width: 12px; height: 12px; flex: none; }
  .contact {
    position: absolute; left: 160px; top: 190px; width: 170px;
    text-align: center;
  }
  .contact__name {
    font-family: "Ubuntu", sans-serif; font-weight: 500;
    font-size: 17px; line-height: 20px; color: var(--ink);
    padding-bottom: 3px; margin-bottom: 3px;
    border-bottom: 2px solid var(--white);
  }
  .contact__line {
    font-family: "Ubuntu", sans-serif;
    font-size: 8px; color: var(--white); line-height: 11px;
  }
  .contact__line span { color: var(--blue); }

  /* Headline side */
  .card--front { left: 560px; top: 350px; }
  .headline-band {
    position: absolute; left: 10px; right: 10px; top: 92px; height: 90px;
    background: var(--amber);
    border: 4px solid var(--white);
    border-radius: 8px;
    display: flex; align-items: center; justify-content: center;
  }
  .headline {
    font-family: "Exo 2", sans-serif; font-weight: 800;
    font-size: 54px; letter-spacing: 1px; line-height: 1;
    color: var(--white);
  }
  .headline__accent { color: var(--blue); }
</style>
</head>
<body>
<main class="canvas">

  <section class="card card--back" aria-label="Business card, contact side">
    <div class="amber-band"></div>
    <div class="brand-label">
      <span class="brand-label__mark"></span>
      <span class="brand-label__name">The Harborline</span>
    </div>
    <ul class="benefits">
      <li><svg viewBox="0 0 12 12"><path d="M1 6.5 L4.5 10 L11 1.5" fill="none" stroke="#fff" stroke-width="2"/></svg>Quality Customer Service</li>
      <li><svg viewBox="0 0 12 12"><path d="M1 6.5 L4.5 10 L11 1.5" fill="none" stroke="#fff" stroke-width="2"/></svg>Email, text or call welcome</li>
    </ul>
    <div class="contact">
      <p class="contact__name">Daniel Moore</p>
      <p class="contact__line">Phone: <span>+610555014</span></p>
      <p class="contact__line">Email: <span>hello@harborline.net</span></p>
    </div>
  </section>

  <section class="card card--front" aria-label="Business card, headline side">
    <div class="headline-band">
      <h1 class="headline">HOME <span class="headline__accent">LOAN</span></h1>
    </div>
  </section>

</main>
</body>
</html>
```